Residential Remodeling Contractor needs updated business card

I need a new design for my business card.
Name of the company is Ridgefell Construction. I need a card that commands presence, strength, integrity. I have been in business for 28 years. I am a Residential Remodeling Contractor that covers all aspects of a residential remodel and build.

```html
<!DOCTYPE html>
<html lang="en">
<head>
<meta charset="utf-8">
<title>Ridgefell Construction – Business Card</title>
<link href="https://fonts.googleapis.com/css2?family=Cinzel:wght@500&family=Montserrat:wght@400;600&display=swap" rel="stylesheet">
<style>
  :root {
    --navy: #213d7e;
    --navy-line: #5a72aa;
    --white: #ffffff;
    --soft: #dfe5f2;
    --stage: #e9e9ec;
  }
  * { box-sizing: border-box; margin: 0; padding: 0; }
  html, body { width: 1200px; height: 786px; overflow: hidden; background: var(--stage); }
  .stage {
    position: relative; width: 1200px; height: 786px;
    display: flex; align-items: center; justify-content: center; gap: 48px;
  }
  .card {
    position: relative; width: 540px; height: 309px;
    background: var(--navy); overflow: hidden;
    box-shadow: 0 6px 18px rgba(0,0,0,.18);
    color: var(--white);
  }
  /* back side */
  .card-back .base-band { position: absolute; left: 0; bottom: 0; width: 100%; height: 60px; }
  .brand-lockup {
    position: absolute; left: 38px; top: 112px; width: 190px;
    display: flex; align-items: center; gap: 10px;
  }
  .brand-mark { width: 10px; height: 10px; background: var(--white); flex: none; }
  .brand-name {
    font-family: "Cinzel", serif; font-weight: 500; font-size: 19px;
    line-height: 1.05; letter-spacing: .5px; color: var(--white);
  }
  .divider {
    position: absolute; left: 248px; top: 62px; width: 1px; height: 150px;
    background: var(--navy-line);
  }
  .contact { position: absolute; left: 268px; top: 62px; font-family: "Montserrat", sans-serif; }
  .contact .person { font-weight: 600; font-size: 17px; }
  .contact .role { font-size: 10px; color: var(--soft); margin-top: 2px; }
  .contact .address { font-size: 10.5px; line-height: 1.3; margin-top: 16px; }
  .contact .lines { list-style: none; margin-top: 8px; }
  .contact .lines li {
    display: flex; align-items: center; gap: 9px;
    font-size: 10.5px; line-height: 1; margin-top: 7px;
  }
  .contact .lines svg { width: 11px; height: 11px; flex: none; }
  /* front side */
  .card-front .brand-lockup.large {
    left: 0; top: 0; width: 100%; height: 100%;
    justify-content: center; gap: 16px;
  }
  .card-front .brand-mark { width: 16px; height: 16px; }
  .card-front .brand-name { font-size: 38px; line-height: 1.05; }
</style>
</head>
<body>
<main class="stage">
  <section class="card card-back" aria-label="Business card, contact side">
    <svg class="base-band" viewBox="0 0 540 60" preserveAspectRatio="none" aria-hidden="true">
      <polygon points="0,42 300,42 310,26 540,26 540,60 0,60" fill="#ffffff"/>
      <polygon points="292,42 300,42 310,26 302,26" fill="#213d7e"/>
    </svg>
    <div class="brand-lockup">
      <span class="brand-mark"></span>
      <span class="brand-name">Ridgefell<br>Construction</span>
    </div>
    <div class="divider"></div>
    <div class="contact">
      <p class="person">Daniel Harlow</p>
      <p class="role">Owner</p>
      <p class="address">48 Cedar Bluff Road<br>Brandon, MS 39042</p>
      <ul class="lines">
        <li>
          <svg viewBox="0 0 12 12" aria-hidden="true"><path d="M2.5 1h2l1 2.5-1.3.9a6 6 0 0 0 3.4 3.4l.9-1.3 2.5 1v2a1 1 0 0 1-1 1A9 9 0 0 1 1.5 2a1 1 0 0 1 1-1z" fill="#fff"/></svg>
          555.014.2290
        </li>
        <li>
          <svg viewBox="0 0 12 12" aria-hidden="true"><rect x="1" y="2.5" width="10" height="7" fill="#fff"/><path d="M1 2.5l5 4 5-4" fill="none" stroke="#213d7e" stroke-width="1"/></svg>
          info@ridgefellconstruction.com
        </li>
        <li>
          <svg viewBox="0 0 12 12" aria-hidden="true"><circle cx="6" cy="6" r="5" fill="none" stroke="#fff" stroke-width="1.2"/><ellipse cx="6" cy="6" rx="2.2" ry="5" fill="none" stroke="#fff" stroke-width="1"/><path d="M1 6h10" stroke="#fff" stroke-width="1"/></svg>
          www.ridgefellconstruction.com
        </li>
      </ul>
    </div>
  </section>

  <section class="card card-front" aria-label="Business card, brand side">
    <div class="brand-lockup large">
      <span class="brand-mark"></span>
      <span class="brand-name">Ridgefell<br>Construction</span>
    </div>
  </section>
</main>
</body>
</html>
```